Our companies name is The Gilded Ladle and we specialize in craft cupcakes, what I mean by that is that we bake our cupcakes with craft beer and other alcoholic drinks. We are trying to focus on being elegant but at the same time unpretentious. Since we are incorporating beer in our cupcakes we want the business card to have our logo in the front and our information in the back.

Once we select the best design we will provide the contact information to be added. Thank you.

Industry/Entity Type

Business

Font styles to use
Decorative
Script

Requirements
Must have
• Round corners
Should not have
• Square corners

```html
<!DOCTYPE html>
<html lang="en">
<head>
<meta charset="utf-8">
<title>The Gilded Ladle – Business Card</title>
<link rel="stylesheet" href="https://fonts.googleapis.com/css2?family=Exo+2:wght@400;600&display=swap">
<style>
  :root {
    --bg: #e9e9e9;
    --card: #ffffff;
    --teal: #82cdc0;
    --red: #e8262c;
    --ink: #1f1f1f;
    --white: #ffffff;
  }
  * { margin: 0; padding: 0; box-sizing: border-box; }
  html, body {
    width: 1200px; height: 771px; overflow: hidden;
    background: var(--bg);
    font-family: "Exo 2", sans-serif;
  }
  .canvas {
    position: relative; width: 1200px; height: 771px;
  }
  .card {
    position: absolute; left: 290px;
    width: 620px; height: 354px;
    background: var(--card);
    border-radius: 18px;
    overflow: hidden;
    box-shadow: 0 2px 8px rgba(0,0,0,0.12);
  }
  .card--front { top: 24px; }
  .card--back { top: 393px; }

  .brand {
    position: absolute;
    display: flex; align-items: center; gap: 10px;
    color: var(--ink);
    font-weight: 600;
    text-transform: uppercase;
    letter-spacing: 1px;
    white-space: nowrap;
  }
  .brand__dot {
    border-radius: 50%;
    background: var(--red);
    flex: none;
  }
  .card--front .brand {
    left: 50%; top: 50%;
    transform: translate(-50%, -50%);
    font-size: 26px;
  }
  .card--front .brand__dot { width: 22px; height: 22px; }

  .back-shape {
    position: absolute; inset: 0;
    width: 620px; height: 354px;
  }
  .card--back .brand {
    left: 418px; top: 218px;
    font-size: 17px;
  }
  .card--back .brand__dot { width: 16px; height: 16px; }

  .contact {
    position: absolute; left: 32px; top: 26px;
    color: var(--white);
  }
  .contact__name {
    color: var(--red);
    font-size: 17px; font-weight: 600;
    letter-spacing: 1.5px; text-transform: uppercase;
  }
  .contact__title {
    font-size: 12px; letter-spacing: 0.5px; margin-top: 1px;
  }
  .contact__address {
    font-size: 12px; line-height: 1.5; margin-top: 22px;
    letter-spacing: 0.5px;
  }
  .contact__list {
    list-style: none; margin-top: 22px;
    font-size: 12px; letter-spacing: 0.5px;
  }
  .contact__list li {
    display: flex; align-items: center; gap: 10px;
    height: 20px;
  }
  .icon { width: 12px; height: 12px; flex: none; }
  .icon * { fill: var(--red); }
</style>
</head>
<body>
<main class="canvas">

  <section class="card card--front" aria-label="Business card front">
    <div class="brand"><span class="brand__dot"></span>The Gilded Ladle</div>
  </section>

  <section class="card card--back" aria-label="Business card back">
    <svg class="back-shape" viewBox="0 0 620 354" aria-hidden="true">
      <path d="M0 0 H392 Q318 120 300 354 H0 Z" fill="var(--teal)"/>
      <path d="M392 0 H420 Q345 110 318 354 H300 Q318 120 392 0 Z" fill="var(--card)"/>
      <path d="M420 0 H452 Q362 105 322 354 H318 Q345 110 420 0 Z" fill="var(--red)"/>
    </svg>

    <div class="contact">
      <p class="contact__name">Maya Ellison</p>
      <p class="contact__title">Managing Director</p>
      <p class="contact__address">14 Copper Lane, Suite 2<br>Harbour Street East</p>
      <ul class="contact__list">
        <li><svg class="icon" viewBox="0 0 12 12"><path d="M2 1 L4.5 1 L5.5 3.5 L4 4.6 Q5 7 7.4 8 L8.5 6.5 L11 7.5 L11 10 Q11 11 10 11 Q1 10.5 1 2 Q1 1 2 1 Z"/></svg>020 555 0143</li>
        <li><svg class="icon" viewBox="0 0 12 12"><path d="M3 0 H9 Q10 0 10 1 V11 Q10 12 9 12 H3 Q2 12 2 11 V1 Q2 0 3 0 Z M3.5 1.5 V9 H8.5 V1.5 Z"/></svg>020 555 0143</li>
        <li><svg class="icon" viewBox="0 0 12 12"><path d="M0 2 H12 V10 H0 Z"/></svg>020 555 0143</li>
        <li><svg class="icon" viewBox="0 0 12 12"><path d="M0 2 H12 V10 H0 Z M1 3 L6 7 L11 3 V2.6 L6 6.2 L1 2.6 Z" fill-rule="evenodd"/></svg>hello@gildedladle.com</li>
        <li><svg class="icon" viewBox="0 0 12 12"><path d="M6 0 A6 6 0 1 1 5.99 0 Z M6 2 A4 4 0 1 0 6.01 2 Z" fill-rule="evenodd"/></svg>www.gildedladle.com</li>
      </ul>
    </div>

    <div class="brand"><span class="brand__dot"></span>The Gilded Ladle</div>
  </section>

</main>
</body>
</html>
```